Classy, Elegant, Simple Business Card Design

Looking to have a classy, simple, and elegant design. Want a top notch designed business card. I really like the look of the new torvane credit card. I also like the design I attached. I am trying to reach 21-29 year old females for booking us for there wedding or event. We offer Disc Jockey Service, Photo Booth Rentals, and Uplighting .

Target Market(s)

21-28 year old females

Contact Information for Business Card

Has to have logo, website, email, and phone number

Font styles to use
Other font styles liked:
• open to font choice, modern, clean
Designer to choose
33a6d7
0791cd
0555a3
ffffff

Requirements
Must have
• Has to have logo, website, email, and phone number
Nice to have
• I really like the design of the new torvane credit card. I also included my logo and some designs I like
Should not have
• clutter or too much info

```html
<!DOCTYPE html>
<html lang="en">
<head>
<meta charset="utf-8">
<title>Tidewell Event Group – Business Card</title>
<link href="https://fonts.googleapis.com/css2?family=Open+Sans:wght@400;600&display=swap" rel="stylesheet">
<style>
  :root {
    --stage: #3b3b3d;
    --card: #13305a;
    --card-deep: #0f2a50;
    --accent: #1f90d8;
    --accent-light: #33a6d7;
    --accent-dark: #0555a3;
    --ink: #ffffff;
    --rule: #8a99ad;
  }
  * { box-sizing: border-box; margin: 0; padding: 0; }
  html, body {
    width: 1200px; height: 1021px; overflow: hidden;
    background: var(--stage);
    font-family: "Open Sans", sans-serif;
    color: var(--ink);
  }
  .stage {
    position: relative; width: 1200px; height: 1021px;
  }
  .card {
    position: absolute; left: 220px; width: 760px; height: 434px;
    background: var(--card);
    overflow: hidden;
    box-shadow: 0 14px 30px rgba(0,0,0,.45);
  }
  .card--front { top: 58px; }
  .card--back { top: 530px; }

  /* front */
  .front-wave {
    position: absolute; inset: 0;
  }
  .front-brand {
    position: absolute; left: 70px; top: 178px;
    display: flex; align-items: center; gap: 16px;
  }
  .brand-dot {
    width: 22px; height: 22px; border-radius: 50%;
    background: var(--accent);
  }
  .front-brand .brand-name {
    font-size: 34px; font-weight: 600; letter-spacing: 3px;
    color: var(--accent-light); text-transform: uppercase;
  }

  /* back */
  .back-brand {
    position: absolute; left: 62px; top: 176px; width: 250px;
    display: flex; align-items: center; gap: 12px;
  }
  .back-brand .brand-dot { width: 16px; height: 16px; flex: none; }
  .back-brand .brand-name {
    font-size: 22px; font-weight: 600; letter-spacing: 2px;
    line-height: 1.25; color: var(--accent-light); text-transform: uppercase;
  }
  .divider {
    position: absolute; left: 340px; top: 110px; width: 2px; height: 160px;
    background: var(--rule);
  }
  .contact {
    position: absolute; left: 380px; top: 118px;
  }
  .contact__name {
    font-size: 24px; font-weight: 600; color: var(--accent);
    letter-spacing: .5px;
  }
  .contact__role { font-size: 19px; margin-top: -2px; }
  .contact__list { list-style: none; margin-top: 18px; }
  .contact__list li {
    display: flex; align-items: center; gap: 10px;
    font-size: 19px; line-height: 28px;
  }
  .contact__list svg { width: 18px; height: 18px; flex: none; }
  .address {
    position: absolute; left: 0; right: 0; top: 330px;
    text-align: center; font-size: 19px; letter-spacing: .3px;
  }
</style>
</head>
<body>
<main class="stage">

  <section class="card card--front" aria-label="Card front">
    <svg class="front-wave" viewBox="0 0 760 434" aria-hidden="true">
      <path d="M-20 340 C 180 250, 420 420, 780 230" fill="none" stroke="var(--accent-dark)" stroke-width="22" opacity=".7"/>
      <path d="M-20 370 C 200 290, 440 450, 780 270" fill="none" stroke="var(--accent)" stroke-width="8" opacity=".6"/>
    </svg>
    <div class="front-brand">
      <span class="brand-dot"></span>
      <span class="brand-name">Tidewell Event Group</span>
    </div>
  </section>

  <section class="card card--back" aria-label="Card back">
    <div class="back-brand">
      <span class="brand-dot"></span>
      <span class="brand-name">Tidewell<br>Event Group</span>
    </div>
    <div class="divider"></div>
    <div class="contact">
      <p class="contact__name">Daniel Reyes</p>
      <p class="contact__role">Founder</p>
      <ul class="contact__list">
        <li>
          <svg viewBox="0 0 24 24"><path d="M6.6 10.8a15 15 0 0 0 6.6 6.6l2.2-2.2a1 1 0 0 1 1-.25 11.4 11.4 0 0 0 3.6.57 1 1 0 0 1 1 1V20a1 1 0 0 1-1 1A17 17 0 0 1 3 4a1 1 0 0 1 1-1h3.5a1 1 0 0 1 1 1c0 1.25.2 2.45.57 3.57a1 1 0 0 1-.25 1z" fill="var(--accent)"/></svg>
          (555) 014-2298
        </li>
        <li>
          <svg viewBox="0 0 24 24"><rect x="2.5" y="5" width="19" height="14" fill="none" stroke="var(--accent)" stroke-width="2"/><path d="M3 6l9 7 9-7" fill="none" stroke="var(--accent)" stroke-width="2"/></svg>
          daniel@tidewell.com
        </li>
        <li>
          <svg viewBox="0 0 24 24" fill="none" stroke="var(--accent)" stroke-width="1.8"><circle cx="12" cy="12" r="9.5"/><ellipse cx="12" cy="12" rx="4" ry="9.5"/><path d="M2.5 12h19M4 7h16M4 17h16"/></svg>
          www.tidewell.com
        </li>
      </ul>
    </div>
    <p class="address">48 Harbor Lane, Suite 310, Coral Bay, Florida, 30412</p>
  </section>

</main>
</body>
</html>
```